Corvex Hiring Partners Business Cards

Business cards with logo design for a new recruiting company called "Corvex Hiring Partners"

incorporate RED & BLUE colors

Final design should reflect strength - clean, elegant design

Company name superimposed upon graphic (Greek Columns)

Please see attached Photos!!!

Industry/Entity Type

Business

Font styles to use
Decorative

Colors
ec2027
0555a3
85cae6

Requirements
Must have
• Must look very similar to attached design!!!

Want Company name superimposed upon graphic (Greek Columns)

Tag line at bottom must be included:
"Empowering Exceptional Companies with Exceptional People"

```html
<!DOCTYPE html>
<html lang="en">
<head>
<meta charset="UTF-8">
<title>Corvex Hiring Partners – Business Card</title>
<link rel="stylesheet" href="https://fonts.googleapis.com/css2?family=Crimson+Pro:wght@400;500&display=swap">
<style>
  :root {
    --brand-red: #ec2027;
    --brand-blue: #0555a3;
    --brand-sky: #85cae6;
    --ink: #1c1c1c;
    --card: #ffffff;
    --backdrop: #e9e6e2;
    --mark-grey: #c9ced6;
  }
  * { box-sizing: border-box; margin: 0; padding: 0; }
  html, body {
    width: 1200px;
    height: 845px;
    overflow: hidden;
    background: var(--backdrop);
  }
  .canvas {
    position: relative;
    width: 1200px;
    height: 845px;
  }
  .card {
    position: absolute;
    left: 100px;
    top: 137px;
    width: 1000px;
    height: 571px;
    background: var(--card);
    box-shadow: 0 10px 30px rgba(0,0,0,0.18);
    font-family: "Crimson Pro", Georgia, serif;
  }
  .brand {
    position: absolute;
    left: 56px;
    top: 48px;
    display: flex;
    align-items: center;
    gap: 26px;
  }
  .brand-dot {
    width: 64px;
    height: 64px;
    border-radius: 50%;
    background: var(--mark-grey);
    flex: none;
  }
  .brand-name {
    color: var(--brand-blue);
    font-size: 58px;
    font-weight: 400;
    line-height: 1.02;
  }
  .person {
    position: absolute;
    left: 76px;
    top: 318px;
    color: var(--brand-blue);
    font-size: 46px;
    font-weight: 400;
  }
  .contacts {
    position: absolute;
    left: 80px;
    top: 398px;
    list-style: none;
    color: var(--ink);
    font-size: 27px;
    line-height: 1;
  }
  .contacts li {
    display: flex;
    align-items: center;
    gap: 14px;
    margin-bottom: 16px;
  }
  .contacts svg {
    width: 24px;
    height: 24px;
    flex: none;
  }
  .tagline {
    position: absolute;
    right: 60px;
    top: 300px;
    text-align: right;
    color: var(--brand-red);
    font-size: 39px;
    line-height: 1.22;
    font-weight: 400;
  }
</style>
</head>
<body>
<main class="canvas">
  <section class="card" aria-label="Business card">
    <div class="brand">
      <span class="brand-dot" aria-hidden="true"></span>
      <h1 class="brand-name">Corvex<br>Hiring<br>Partners</h1>
    </div>

    <p class="person">Daniel R. Whitmore</p>

    <ul class="contacts">
      <li>
        <svg viewBox="0 0 24 24" aria-hidden="true">
          <circle cx="12" cy="12" r="10.5" fill="none" stroke="#1c1c1c" stroke-width="1.6"/>
          <path d="M8.6 6.8c.5-.4 1.2-.3 1.5.2l1 1.6c.3.5.2 1.1-.2 1.4l-.7.6c.5 1.3 1.6 2.6 3 3.3l.6-.7c.4-.4 1-.5 1.4-.2l1.6 1c.5.3.6 1 .2 1.5l-.7.8c-.6.6-1.6.8-2.5.4-2.7-1.2-4.7-3.3-5.8-6-.3-.9-.1-1.9.5-2.5z" fill="#1c1c1c"/>
        </svg>
        <span>512-555-0147</span>
      </li>
      <li>
        <svg viewBox="0 0 24 24" aria-hidden="true">
          <circle cx="12" cy="12" r="11" fill="#1c1c1c"/>
          <rect x="6" y="8" width="12" height="8.5" rx="1" fill="#fff"/>
          <path d="M6.4 8.5 12 13l5.6-4.5" fill="none" stroke="#1c1c1c" stroke-width="1.3"/>
        </svg>
        <span>DWhitmore@CorvexHP.com</span>
      </li>
      <li>
        <svg viewBox="0 0 24 24" aria-hidden="true">
          <circle cx="12" cy="12" r="10" fill="none" stroke="#1c1c1c" stroke-width="2"/>
          <ellipse cx="12" cy="12" rx="4.2" ry="10" fill="none" stroke="#1c1c1c" stroke-width="1.6"/>
          <path d="M2.5 9h19M2.5 15h19M12 2v20" stroke="#1c1c1c" stroke-width="1.6"/>
        </svg>
        <span>www.CorvexHP.com</span>
      </li>
    </ul>

    <p class="tagline">Empowering<br>Exceptional Companies<br>with Exceptional People</p>
  </section>
</main>
</body>
</html>
```